Design a modern, classy & professional business card for an online real estate agency, specializing in medium-luxury properties in Thailand and later in Singapore and UK.

Possible design ideas so far: (not essential)

- curved corner(s) to the card, white on front & turquoise on back or visa versa.

- front of card - clear and simple, company name in metallic grey/monochrome, logo graphic & company name on front in spot UV or embossed/debossed effect.

- back of card - large, close-cropped, 'ghost' patterns of the C-shaped curves of logo, or company name repeated on back of card in spot UV.

Target Market(s)

- young to middle-aged professionals mainly (but ideally should design should suit all)

- UK, US,EU,AUS & ASIAN mainly (but ideally should design should suit all countries)

Industry/Entity Type

Real Estate

Requirements
Must have
• THEME:
- Luxurious & Modern
- Clean & striking
- Unique & creative

INFO:
- Logo & company name on front
- Contact details on back:

Tobias Hennlund
Managing Director

www.velmontestates.asia
www.velmontestates.co.uk

Tel: 083-274-6159
email: tobias@velmontestates.asia

(contact details can be displayed in any order as suites design.)

Nice to have
• - curved corner(s) to the card, white on front & turquoise on back or visa versa.

Should not have
• - No generic images of properties, palm trees/coconut trees etc.

- No other other bold colors, except for main turquoise, grey, metallic white & black theme.

- No obvious business card templates

```html
<!DOCTYPE html>
<html lang="en">
<head>
<meta charset="utf-8">
<title>Velmont Estates – Business Card</title>
<link href="https://fonts.googleapis.com/css2?family=Cormorant+Garamond:wght@500&family=PT+Serif&family=Ubuntu:ital,wght@0,700;1,400&display=swap" rel="stylesheet">
<style>
  :root {
    --bg: #e6e7e8;
    --turquoise: #74c2bc;
    --turquoise-dark: #5aa9a4;
    --grey: #6f6f6f;
    --grey-dark: #4a4a4a;
    --white: #ffffff;
    --paper: #f6f6f6;
    --text: #2f2f2f;
  }
  * { margin: 0; padding: 0; box-sizing: border-box; }
  html, body { width: 1200px; height: 675px; overflow: hidden; }
  body {
    background: var(--bg);
    position: relative;
    font-family: "PT Serif", Georgia, serif;
  }
  .card {
    position: absolute;
    top: 187px;
    width: 525px;
    height: 300px;
    overflow: hidden;
    box-shadow: 0 6px 18px rgba(0,0,0,0.12);
  }
  /* Front */
  .card-front {
    left: 45px;
    background: var(--turquoise);
    display: flex;
    align-items: center;
    justify-content: center;
    gap: 20px;
  }
  .brand-mark {
    width: 78px;
    height: 78px;
    background: var(--white);
    flex: none;
  }
  .brand-name {
    font-family: "Cormorant Garamond", Georgia, serif;
    font-weight: 500;
    font-size: 52px;
    color: var(--grey);
    letter-spacing: 0.5px;
    white-space: nowrap;
  }
  /* Back */
  .card-back {
    left: 630px;
    background: var(--paper);
  }
  .pattern-field {
    position: absolute;
    inset: 0;
    background: radial-gradient(ellipse at 70% 40%, #fbfbfb 0%, #efefef 70%, #e9e9e9 100%);
  }
  .back-brand {
    position: absolute;
    left: 34px;
    top: 52px;
    display: flex;
    align-items: center;
    gap: 12px;
  }
  .back-brand .brand-mark {
    width: 50px;
    height: 50px;
    background: var(--turquoise-dark);
  }
  .back-brand .brand-name { font-size: 36px; }
  .contact-list {
    position: absolute;
    left: 290px;
    top: 146px;
    list-style: none;
    font-size: 13px;
    color: var(--text);
  }
  .contact-list li {
    display: flex;
    align-items: center;
    gap: 9px;
    height: 24px;
    white-space: nowrap;
  }
  .contact-list svg { width: 13px; height: 13px; flex: none; fill: var(--grey-dark); }
  .contact-list .accent { color: var(--turquoise-dark); }
  .person {
    position: absolute;
    left: 34px;
    bottom: 44px;
    font-family: "Ubuntu", Arial, sans-serif;
  }
  .person-name {
    font-weight: 700;
    font-size: 17px;
    color: var(--turquoise-dark);
  }
  .person-role {
    font-style: italic;
    font-size: 12.5px;
    color: var(--grey);
    margin-top: 3px;
    padding-left: 22px;
  }
  .edge-stripe {
    position: absolute;
    right: 0;
    top: 118px;
    width: 130px;
    height: 6px;
    background: var(--grey-dark);
  }
  .accent-rule {
    position: absolute;
    right: 0;
    top: 262px;
    width: 220px;
    height: 3px;
    background: var(--turquoise);
  }
  .base-band {
    position: absolute;
    left: 0;
    right: 0;
    bottom: 0;
    height: 9px;
    background: var(--turquoise);
  }
</style>
</head>
<body>

  <section class="card card-front" aria-label="Card front">
    <span class="brand-mark"></span>
    <span class="brand-name">Velmont Estates</span>
  </section>

  <section class="card card-back" aria-label="Card back">
    <div class="pattern-field" role="img" aria-label="Faint repeating pattern of light grey interlocking circles"></div>

    <div class="back-brand">
      <span class="brand-mark"></span>
      <span class="brand-name">Velmont Estates</span>
    </div>

    <div class="edge-stripe"></div>

    <ul class="contact-list">
      <li>
        <svg viewBox="0 0 16 16" aria-hidden="true"><path d="M3.5 1l2.5 3-1.5 1.8c.8 2 2.4 3.6 4.4 4.4L10.7 8.7l3.3 2.3-.8 3C7 14 2 9 2 2.8z"/></svg>
        <span>083-274-6159</span>
      </li>
      <li>
        <svg viewBox="0 0 16 16" aria-hidden="true"><path d="M1 3h14v10H1zM2.5 4.5L8 9l5.5-4.5v-.3H2.5z" fill-rule="evenodd"/></svg>
        <span>tobias@velmontestates.asia</span>
      </li>
      <li>
        <svg viewBox="0 0 16 16" aria-hidden="true"><circle cx="8" cy="8" r="7"/><path d="M1 8h14M8 1c-3 3.5-3 10.5 0 14M8 1c3 3.5 3 10.5 0 14" stroke="#f6f6f6" stroke-width="1" fill="none"/></svg>
        <span>www.<span class="accent">velmontestates</span>.asia</span>
      </li>
      <li>
        <svg viewBox="0 0 16 16" aria-hidden="true"><circle cx="8" cy="8" r="7"/><path d="M1 8h14M8 1c-3 3.5-3 10.5 0 14M8 1c3 3.5 3 10.5 0 14" stroke="#f6f6f6" stroke-width="1" fill="none"/></svg>
        <span>www.<span class="accent">velmontestates</span>.co.uk</span>
      </li>
    </ul>

    <div class="accent-rule"></div>

    <div class="person">
      <p class="person-name">Tobias Hennlund</p>
      <p class="person-role">Managing Director</p>
    </div>

    <div class="base-band"></div>
  </section>

</body>
</html>
```